Web Design Velmora Tech

• An Overview of Velmora Tech for reference: We use to be a component manufacturing company. We sold to customers in USA and manage the builds in China using many manufacturing partners. We had a web site that served this market but we have transitioned over the last several years into “A unique design, development and program management company” It is this message we want to put up on the web now. We provide the design support, we help develop and test a new product for our customers and we provide the manufactured produce once we have transitioned it into production.
• The Target Market: Our customers are all high tech. Each product we produce is custom designed and sold only to one a specific customer. We work with a limited number of customer and sell to new customers by word of mouth and referrals. The web site is to provide a back ground check of any new referral so they can see who we are and our basic capabilities. It is not designed to sell customers or to find new customers but provide a background check to new potential customers.
• Pages Required: We estimate 12:
o Home/Title page is page 1 of PDF. It would have buttons to select other pages
o Names of other pages would be (short titles below if on button, if pull down menu the full title of slide)
 USA Facilities
 China Facilities
 Enclosures
 Antennas
 Connectors
 Cables
 EMI Shields
 Overlays
 Process Development
 BrisaLink
 Contact Us (???) >> new page which we are not sure if we should or should not add.
• Design Specifics; attached is our logo, a PDF and PowerPoint slides showing the views we desire. We like these layouts, but perhaps a better one may be suggested for some artistic reason or layout. It should be clean, simple and user intuitive. We like the off white background and use for most of our presentations. One should be able to go from any screen to any other screen. The quote must include both design and implementation onto our web site which is http://velmoratechworks.example/
• Design Process:
We would like to see concepts of the Landing/Homepage, and an internal page initially. Feedback will be provided and you will be asked to continue if your layout is on the correct track.

• Implementation: Desire designer/implimentor to set up on their server. Allow us to test and edit on their site. We will provide password for implementation on our site after final approval.

Target Market(s)

• The Target Market: see above task descripiton

Industry/Entity Type

It Company

Requirements
Must have
• • Pages Required: We estimate 12:
 USA Facilities
 China Facilities
 Enclosures
 Antennas
 Connectors
 Cables
 EMI Shields
 Overlays
 Process Development
 BrisaLink

Must have the implementation phase include in quote. see task description above
Should not have
• Should not be complex or long time loading.
Do not want any twitter or promotional add on functions.

```html
<!DOCTYPE html>
<html lang="en">
<head>
<meta charset="utf-8">
<title>Velmora Tech — Design, Development and Program Management</title>
<link rel="stylesheet" href="https://fonts.googleapis.com/css2?family=Arimo:wght@400;700&display=swap">
<style>
  :root {
    --brand: #0a6fc2;
    --brand-deep: #0868b8;
    --accent: #1a8fd6;
    --link: #0a78c8;
    --text: #555b60;
    --muted: #777;
    --line: #e6e6e6;
    --white: #ffffff;
    --hero-top: #2a9be0;
    --hero-bottom: #0b74c4;
  }
  * { box-sizing: border-box; margin: 0; padding: 0; }
  html, body { width: 1096px; height: 1200px; overflow: hidden; background: var(--white); }
  body { font-family: "Arimo", Arial, sans-serif; color: var(--text); }

  .page {
    position: relative;
    width: 1200px;
    height: 1313px;
    transform: scale(0.91333);
    transform-origin: 0 0;
  }
  .abs { position: absolute; }

  .main-nav {
    position: absolute; left: 96px; top: 0; width: 1000px; height: 44px;
    background: var(--brand);
    display: flex; justify-content: space-between; align-items: center;
    padding: 0 10px;
  }
  .main-nav a, .footer-nav a {
    color: var(--white); font-weight: 700; font-size: 12.5px; text-decoration: none; white-space: nowrap;
  }

  .brand {
    position: absolute; left: 96px; top: 60px;
    display: flex; align-items: center; gap: 10px;
  }
  .brand-mark { width: 26px; height: 26px; background: var(--brand); }
  .brand-name { color: var(--brand); font-weight: 700; font-size: 30px; letter-spacing: -0.5px; }

  .search {
    position: absolute; left: 892px; top: 89px; width: 192px; height: 36px;
    border: 1px solid #d0d0d0; box-shadow: inset 0 1px 2px rgba(0,0,0,.08);
    display: flex; align-items: center; justify-content: space-between; padding: 0 12px 0 14px;
    font-size: 12px; color: #999;
  }

  .hero {
    position: absolute; left: 96px; top: 177px; width: 1000px; height: 336px;
    background: radial-gradient(ellipse at 60% 40%, var(--hero-top), var(--hero-bottom) 85%);
  }
  .hero-title {
    position: absolute; left: 68px; top: 75px; width: 380px;
    color: var(--white); font-weight: 700; font-size: 31px; line-height: 38px;
  }
  .hero-product {
    position: absolute; left: 690px; top: 50px; width: 220px; height: 245px;
    border-radius: 18px;
    background: radial-gradient(ellipse at 50% 45%, rgba(255,255,255,.35), rgba(20,60,140,.55) 70%, rgba(11,116,196,0) 100%);
  }
  .hero-arrow {
    position: absolute; top: 142px; width: 20px; height: 40px; background: var(--white);
    display: flex; align-items: center; justify-content: center;
  }
  .hero-arrow.prev { left: 0; border-radius: 0 20px 20px 0; }
  .hero-arrow.next { right: 0; border-radius: 20px 0 0 20px; }
  .hero-dots { position: absolute; left: 78px; top: 306px; display: flex; gap: 10px; }
  .hero-dots span { width: 11px; height: 11px; border-radius: 50%; background: rgba(255,255,255,.75); }

  .service {
    position: absolute; top: 539px; width: 284px; height: 309px;
    border: 1px solid var(--line);
  }
  .service h3 {
    position: absolute; top: 12px; color: var(--accent); font-weight: 700; font-size: 16px; line-height: 18px; letter-spacing: .3px;
  }
  .service .photo { position: absolute; top: 63px; width: 216px; height: 121px; }
  .service p {
    position: absolute; top: 197px; width: 215px; font-size: 12px; line-height: 17px; color: var(--text);
  }
  .read-more { color: var(--link); text-decoration: none; font-size: 12px; display: inline-flex; align-items: center; gap: 6px; }

  .section-title { position: absolute; color: var(--accent); font-weight: 700; font-size: 15px; letter-spacing: .3px; }

  .task-list { position: absolute; left: 140px; top: 917px; list-style: none; }
  .task-list li {
    font-size: 12px; color: var(--muted); height: 25px; display: flex; gap: 13px; align-items: flex-start;
  }
  .task-list svg { margin-top: 3px; flex: none; }

  .feature-icon { position: absolute; }
  .feature-text { position: absolute; left: 543px; width: 530px; font-size: 12px; line-height: 17px; color: var(--text); }
  .feature-text a { color: var(--link); text-decoration: none; }

  .site-footer {
    position: absolute; left: 0; top: 1176px; width: 1200px; height: 137px; background: var(--brand-deep);
    color: var(--white); text-align: center;
  }
  .footer-nav {
    position: absolute; left: 96px; top: 28px; width: 1000px; display: flex; justify-content: space-between; padding: 0 10px;
  }
  .legal { position: absolute; left: 0; top: 54px; width: 1200px; font-size: 12px; line-height: 14px; }
  .legal a { color: var(--white); text-decoration: none; }
  .feed-icon { position: absolute; left: 589px; top: 96px; }
</style>
</head>
<body>
<div class="page">

  <nav class="main-nav">
    <a href="#">Home</a><a href="#">USA Facilities</a><a href="#">China Facilities</a><a href="#">Enclosures</a>
    <a href="#">Antennas</a><a href="#">Connectors</a><a href="#">Cables</a><a href="#">EMI Shields</a>
    <a href="#">Overlays</a><a href="#">Process Development</a><a href="#">BrisaLink</a><a href="#">Contact us</a>
  </nav>

  <a class="brand" href="#"><span class="brand-mark"></span><span class="brand-name">Velmora Tech</span></a>

  <div class="search">
    <span>Search</span>
    <svg width="16" height="16" viewBox="0 0 16 16"><circle cx="6.5" cy="6.5" r="5" fill="none" stroke="#aaa" stroke-width="1.6"/><line x1="10.2" y1="10.2" x2="15" y2="15" stroke="#aaa" stroke-width="2"/></svg>
  </div>

  <section class="hero">
    <h1 class="hero-title">A unique design, development and program management company</h1>
    <div class="hero-product" role="img" aria-label="Photo of two blue handheld test devices"></div>
    <span class="hero-arrow prev"><svg width="8" height="10" viewBox="0 0 8 10"><polygon points="8,0 0,5 8,10" fill="#555"/></svg></span>
    <span class="hero-arrow next"><svg width="8" height="10" viewBox="0 0 8 10"><polygon points="0,0 8,5 0,10" fill="#555"/></svg></span>
    <div class="hero-dots"><span></span><span></span><span></span><span></span></div>
  </section>

  <article class="service" style="left:106px">
    <h3 style="left:31px">CUSTOM ENCLOSURE<br>DESIGN &amp; DEVELOPMENT</h3>
    <div class="photo" role="img" aria-label="Photo of engineers inspecting enclosure parts on a factory line" style="left:29px;background:linear-gradient(135deg,#6c7a6a,#b9b4a4 55%,#b8343a)"></div>
    <p style="left:27px">Sed ut perspiciatis unde omnis iste natus error sit voluptatem accusantium doloremque laudantium natus error sit voluptatem accusantium<br>
      <a class="read-more" href="#">Read more <svg width="10" height="8" viewBox="0 0 10 8"><path d="M0 4h8M5 1l3 3-3 3" stroke="#111" stroke-width="1.6" fill="none"/></svg></a></p>
  </article>

  <article class="service" style="left:452px">
    <h3 style="left:32px">CUSTOM ANTENNA DESIGN<br>&amp; DEVELOPMENT</h3>
    <div class="photo" role="img" aria-label="Photo of engineers in an antenna test chamber" style="left:32px;background:linear-gradient(135deg,#2d6fd0,#1f4fa8 60%,#8a8fb0)"></div>
    <p style="left:32px">Sed ut perspiciatis unde omnis iste natus error sit voluptatem accusantium doloremque laudantium natus error sit voluptatem accusantium<br>
      <a class="read-more" href="#">Read more <svg width="10" height="8" viewBox="0 0 10 8"><path d="M0 4h8M5 1l3 3-3 3" stroke="#111" stroke-width="1.6" fill="none"/></svg></a></p>
  </article>

  <article class="service" style="left:793px">
    <h3 style="left:35px">CUSTOM CONNECTOR<br>DESIGN &amp; DEVELOPMENT</h3>
    <div class="photo" role="img" aria-label="Photo of a connector part on a machining table" style="left:33px;background:linear-gradient(135deg,#3e4046,#c9cac6 55%,#8d8f8c)"></div>
    <p style="left:32px">Sed ut perspiciatis unde omnis iste natus error sit voluptatem accusantium doloremque laudantium natus error sit voluptatem accusantium<br>
      <a class="read-more" href="#">Read more <svg width="10" height="8" viewBox="0 0 10 8"><path d="M0 4h8M5 1l3 3-3 3" stroke="#111" stroke-width="1.6" fill="none"/></svg></a></p>
  </article>

  <h2 class="section-title" style="left:115px;top:877px">WHAT WE DO?</h2>
  <ul class="task-list">
    <li><svg width="8" height="6" viewBox="0 0 8 6"><path d="M0 3h7M4.5 .5 7 3 4.5 5.5" stroke="#333" stroke-width="1" fill="none"/></svg>Nulla facilisi. Aenean nec eros</li>
    <li><svg width="8" height="6" viewBox="0 0 8 6"><path d="M0 3h7M4.5 .5 7 3 4.5 5.5" stroke="#333" stroke-width="1" fill="none"/></svg>Vestib ulum ante ips um primis in fau</li>
    <li><svg width="8" height="6" viewBox="0 0 8 6"><path d="M0 3h7M4.5 .5 7 3 4.5 5.5" stroke="#333" stroke-width="1" fill="none"/></svg>Susp endisse sollici udin velit sed leo</li>
    <li><svg width="8" height="6" viewBox="0 0 8 6"><path d="M0 3h7M4.5 .5 7 3 4.5 5.5" stroke="#333" stroke-width="1" fill="none"/></svg>Ut pharetra augue nec augu elit mag</li>
    <li><svg width="8" height="6" viewBox="0 0 8 6"><path d="M0 3h7M4.5 .5 7 3 4.5 5.5" stroke="#333" stroke-width="1" fill="none"/></svg>Donec porta diam eu massa</li>
    <li><svg width="8" height="6" viewBox="0 0 8 6"><path d="M0 3h7M4.5 .5 7 3 4.5 5.5" stroke="#333" stroke-width="1" fill="none"/></svg>Quisque diam lorem interdum vitae</li>
    <li><svg width="8" height="6" viewBox="0 0 8 6"><path d="M0 3h7M4.5 .5 7 3 4.5 5.5" stroke="#333" stroke-width="1" fill="none"/></svg>Donec eget tellus non erat lacinia fer</li>
    <li><svg width="8" height="6" viewBox="0 0 8 6"><path d="M0 3h7M4.5 .5 7 3 4.5 5.5" stroke="#333" stroke-width="1" fill="none"/></svg>Donec in velit vel ipsum auctorulvina</li>
  </ul>

  <h2 class="section-title" style="left:456px;top:877px">ABOUT OUR COMPANY</h2>
  <svg class="feature-icon" style="left:467px;top:930px" width="49" height="36" viewBox="0 0 49 36">
    <path d="M1 2h15l4 5h22v6H1z" fill="#1a8fd6"/>
    <path d="M5 13h43l-6 22H1z" fill="#3aa6e2"/>
  </svg>
  <p class="feature-text" style="top:917px">Nulla facilisi. Aenean nec eros. Vestib ulum ante ips um primis in fau ciburci luctus et ultrics posu ere cubilia Susp endisse sollict udin velit sed leo. Ut pharetra augue nec augu elit magnan drerit sit amet tinci dunt aiverra sed nullanec porta diam eu massa. Quisque diam interdum vitaedapi bus ac celerisque vitae pede. Donec eget tellus non erat lacinia ferme ntum. <a href="#">Read more..</a></p>

  <h2 class="section-title" style="left:456px;top:1018px">WHY US?</h2>
  <svg class="feature-icon" style="left:471px;top:1066px" width="45" height="38" viewBox="0 0 45 38">
    <path d="M4 0h26a4 4 0 0 1 4 4v14a4 4 0 0 1-4 4H14l-8 7v-7H4a4 4 0 0 1-4-4V4a4 4 0 0 1 4-4z" fill="#1a8fd6"/>
    <path d="M37 9h4a4 4 0 0 1 4 4v13a4 4 0 0 1-4 4h-2v7l-8-7H20a4 4 0 0 1-4-4v-1h17a4 4 0 0 0 4-4z" fill="#1a8fd6"/>
  </svg>
  <p class="feature-text" style="top:1048px">Nulla facilisi. Aenean nec eros. Vestib ulum ante ips um primis in fau ciburci luctus et ultrics posu ere cubilia Susp endisse sollict udin velit sed leo. Ut pharetra augue nec augu elit magnan drerit sit amet tinci dunt aiverra sed nullanec porta diam eu massa. Quisque diam interdum vitaedapi bus ac celerisque vitae pede. Donec eget tellus non erat lacinia ferme ntum. <a href="#">Read more..</a></p>

  <footer class="site-footer">
    <nav class="footer-nav">
      <a href="#">Home</a><a href="#">USA Facilities</a><a href="#">China Facilities</a><a href="#">Enclosures</a>
      <a href="#">Antennas</a><a href="#">Connectors</a><a href="#">Cables</a><a href="#">EMI Shields</a>
      <a href="#">Overlays</a><a href="#">Process Development</a><a href="#">BrisaLink</a><a href="#">Contact us</a>
    </nav>
    <div class="legal">COPYRIGHT 2013. ALL RIGHTS RESERVED.<br>
      <a href="#">TERMS &amp; CONDITIONS</a> &nbsp;-&nbsp; <a href="#">PRIVACY</a> &nbsp;-&nbsp; <a href="#">DISCLAIMER</a></div>
    <svg class="feed-icon" width="22" height="22" viewBox="0 0 22 22" aria-label="Feed">
      <circle cx="3" cy="19" r="3" fill="#fff"/>
      <path d="M0 9a13 13 0 0 1 13 13M0 1a21 21 0 0 1 21 21" stroke="#fff" stroke-width="3" fill="none"/>
    </svg>
  </footer>

</div>
</body>
</html>
```